Road Construction Company needs business cards

We would like a new business card designed for our business.

We're a road construction company based in Qld, Australia.

Can the business card please have the following information on it.

Name: Warren Halbeck
Position: General Manager
Phone: 0472 915 348
Email: Warren.halbeck@tovrin.com.au
Address: 87 Marrow Ave, Pendlebay, QLD, 4023
Website: www.tovrin.com.au

Visually we'd like the card to be professional and simple.

Attached is our logo.

Our website is www.tovrin.com.au

Target Market(s)

Men aged 25-60

Contact Information for Business Card

As listed in project description

Font styles to use
Serif

Requirements
Must have
• Large logo on back of card

```html
<!DOCTYPE html>
<html lang="en">
<head>
<meta charset="utf-8">
<title>Tovrin Business Card</title>
<link rel="stylesheet" href="https://fonts.googleapis.com/css2?family=Libre+Bodoni:wght@400;700&display=swap">
<style>
  :root {
    --page-bg: #8da7c2;
    --navy: #061f3a;
    --white: #ffffff;
    --silver-light: #f4f5f6;
    --silver-mid: #dcdee0;
    --silver-dark: #b9bcc0;
    --muted-grey: #a3a6aa;
    --icon-grey: #9c9fa4;
    --brand-blue: #1560b0;
  }
  * { margin: 0; padding: 0; box-sizing: border-box; }
  html, body {
    width: 1200px;
    height: 892px;
    overflow: hidden;
    background: var(--page-bg);
    font-family: "Libre Bodoni", Georgia, serif;
  }
  .canvas {
    position: relative;
    width: 1200px;
    height: 892px;
  }
  .card {
    position: absolute;
    top: 290px;
    width: 540px;
    height: 310px;
    overflow: hidden;
    box-shadow: 0 18px 36px rgba(40, 70, 100, 0.25);
  }
  /* Front */
  .card-front {
    left: 40px;
    background: var(--navy);
    color: var(--white);
  }
  .accent-bar {
    position: absolute;
    height: 17px;
    background: var(--white);
  }
  .accent-bar--left { left: 0; top: 78px; width: 108px; }
  .accent-bar--right { right: 0; top: 136px; width: 112px; }
  .identity {
    position: absolute;
    left: 128px;
    top: 70px;
    width: 290px;
    text-align: center;
  }
  .person-name {
    font-weight: 700;
    font-size: 27px;
    letter-spacing: 0.5px;
    text-transform: uppercase;
    line-height: 1.1;
  }
  .person-role {
    font-size: 19px;
    color: var(--muted-grey);
    margin-top: 2px;
  }
  .contact-list {
    position: absolute;
    left: 32px;
    top: 168px;
    list-style: none;
    font-size: 14px;
    line-height: 22px;
  }
  .contact-list li {
    display: flex;
    align-items: center;
    gap: 9px;
  }
  .contact-icon {
    width: 13px;
    height: 13px;
    flex: none;
    fill: none;
    stroke: var(--icon-grey);
    stroke-width: 1.6;
  }
  .front-wordmark {
    position: absolute;
    right: 34px;
    bottom: 30px;
    font-size: 30px;
    font-weight: 700;
    letter-spacing: 3px;
    color: var(--muted-grey);
  }
  /* Back */
  .card-back {
    left: 620px;
    background: linear-gradient(110deg, var(--silver-light) 0%, var(--white) 38%, var(--silver-mid) 70%, var(--silver-dark) 100%);
    display: flex;
    align-items: center;
    justify-content: center;
  }
  .back-wordmark {
    font-size: 76px;
    font-weight: 700;
    letter-spacing: 6px;
    color: var(--brand-blue);
  }
</style>
</head>
<body>
<main class="canvas">
  <section class="card card-front" aria-label="Business card front">
    <div class="accent-bar accent-bar--left"></div>
    <div class="accent-bar accent-bar--right"></div>
    <header class="identity">
      <h1 class="person-name">Warren Halbeck</h1>
      <p class="person-role">General Manager</p>
    </header>
    <ul class="contact-list">
      <li>
        <svg class="contact-icon" viewBox="0 0 16 16" aria-hidden="true"><path d="M4 1.5l2.2 3-1.3 1.6c.8 1.9 2.3 3.4 4.2 4.2l1.6-1.3 3 2.2-1.2 2.6C7.200 13.500 2.500 8.800 1.500 3z"/></svg>
        0472 915 348
      </li>
      <li>
        <svg class="contact-icon" viewBox="0 0 16 16" aria-hidden="true"><circle cx="8" cy="8" r="2.8"/><path d="M10.8 8v1.2c0 1.8 3.4 1.8 3.4-1.2A6.2 6.2 0 1 0 11 13.4"/></svg>
        Warren.halbeck@tovrin.com.au
      </li>
      <li>
        <svg class="contact-icon" viewBox="0 0 16 16" aria-hidden="true"><path d="M8 15s5-5 5-8.5A5 5 0 0 0 3 6.5C3 10 8 15 8 15z"/><circle cx="8" cy="6.5" r="1.7"/></svg>
        87 Marrow Ave, Pendlebay, QLD, 4023
      </li>
      <li>
        <svg class="contact-icon" viewBox="0 0 16 16" aria-hidden="true"><circle cx="8" cy="8" r="6.5"/><path d="M1.5 8h13M8 1.5c2.2 2.4 2.2 10.6 0 13M8 1.5c-2.2 2.4-2.2 10.6 0 13"/></svg>
        www.tovrin.com.au
      </li>
    </ul>
    <div class="front-wordmark">TOVRIN</div>
  </section>

  <section class="card card-back" aria-label="Business card back">
    <div class="back-wordmark">TOVRIN</div>
  </section>
</main>
</body>
</html>
```